Oil Field Service company needs professional business cards

Looking to clean up our current company business cards and look a little more professional. Brenwick Casing Services is a US based company that services the oil field. We deal with engineers, managers and oil rigs....................................................................................................................................................................................................................................................................................................................................................................................................

Target Market(s)

Oil and Gas professionals

Industry/Entity Type

Oil And Gas

Contact Information for Business Card

See attached photo as example

Font styles to use
Sans Serif

Colors
ec1f27

Requirements
Must have
• Company Logo, Name, Title, Cell, Office, Fax, Email.
• See attached photo
Nice to have
• External CRT, Internal CRT, Casing Crews, Torque Turn, Laydown Machine
Should not have
• Do not introduce any new pictures and keep it professional looking

```html
<!DOCTYPE html>
<html lang="en">
<head>
<meta charset="utf-8">
<title>Brenwick Casing Services – Business Cards</title>
<link rel="stylesheet" href="https://fonts.googleapis.com/css2?family=Arimo:wght@400;700&family=Oswald:wght@400&family=Roboto+Condensed:wght@400&display=swap">
<style>
  :root {
    --red: #ec1f27;
    --band-red: #d7262b;
    --slate: #3d5163;
    --ink: #333b42;
    --muted: #5a6269;
    --card: #f7f7f6;
    --backdrop: #e4e4e3;
  }
  * { margin: 0; padding: 0; box-sizing: border-box; }
  html, body { width: 1200px; height: 576px; overflow: hidden; background: var(--backdrop); }
  .sheet { position: relative; width: 1200px; height: 576px; }

  .card {
    position: absolute; top: 140px; width: 484px; height: 292px;
    background: var(--card); border-radius: 6px; overflow: hidden;
    font-family: "Arimo", Arial, sans-serif;
  }
  .card--front { left: 82px; }
  .card--back { left: 602px; }

  /* company name */
  .brand { position: absolute; color: var(--slate); font-weight: 700; text-align: center; }
  .brand__name { display: block; letter-spacing: 1px; line-height: 1; }
  .brand__line { display: block; letter-spacing: 3px; line-height: 1; }
  .card--front .brand { left: 0; right: 0; top: 82px; }
  .card--front .brand__name { font-size: 52px; }
  .card--front .brand__line { font-size: 17px; margin-top: 18px; }
  .card--back .brand { right: 22px; top: 38px; width: 230px; }
  .card--back .brand__name { font-size: 38px; }
  .card--back .brand__line { font-size: 12.5px; margin-top: 14px; letter-spacing: 2.4px; }

  /* front */
  .services {
    position: absolute; left: 0; right: 0; top: 220px; height: 27px;
    background: var(--band-red); color: #fff; font-weight: 700; font-size: 12.5px;
    display: flex; align-items: center; justify-content: center; gap: 8px; letter-spacing: .2px;
  }
  .services__sep { opacity: .9; }
  .website {
    position: absolute; left: 0; right: 0; top: 261px;
    display: flex; align-items: center; justify-content: center; gap: 10px;
    font-size: 13px; color: var(--ink);
  }
  .website__rule { width: 70px; height: 2px; background: var(--red); }

  /* back */
  .tab { position: absolute; left: -21px; top: 164px; width: 42px; height: 42px; border-radius: 50%; background: var(--red); }
  .person { position: absolute; left: 24px; top: 166px; }
  .person__name { font-family: "Oswald", sans-serif; font-size: 21px; color: var(--ink); line-height: 1.1; }
  .person__title { font-size: 11px; color: var(--muted); margin-top: 3px; }

  .contacts {
    position: absolute; left: 26px; top: 236px;
    display: grid; grid-template-columns: 108px 124px auto; row-gap: 4px;
    font-family: "Roboto Condensed", sans-serif; font-size: 11.5px; color: var(--ink);
  }
  .contact { display: flex; align-items: center; gap: 7px; white-space: nowrap; }
  .contact svg { width: 10px; height: 10px; fill: var(--red); flex: none; }
</style>
</head>
<body>
<main class="sheet">

  <section class="card card--front" aria-label="Card front">
    <div class="brand">
      <span class="brand__name">BRENWICK</span>
      <span class="brand__line">CASING SERVICES</span>
    </div>
    <div class="services">
      <span>LAYDOWN MACHINE</span><span class="services__sep">|</span>
      <span>CASING CREW</span><span class="services__sep">|</span>
      <span>MUD TOOL</span><span class="services__sep">|</span>
      <span>TORQUE TURN</span>
    </div>
    <div class="website">
      <span class="website__rule"></span>
      <span>www.brenwicksrvs.com</span>
      <span class="website__rule"></span>
    </div>
  </section>

  <section class="card card--back" aria-label="Card back">
    <div class="brand">
      <span class="brand__name">BRENWICK</span>
      <span class="brand__line">CASING SERVICES</span>
    </div>
    <span class="tab"></span>
    <div class="person">
      <p class="person__name">Cody Harlan</p>
      <p class="person__title">Area Manager</p>
    </div>
    <div class="contacts">
      <span class="contact">
        <svg viewBox="0 0 10 10" aria-hidden="true"><path d="M2 0.5 L3.6 2.8 L2.8 3.8 C3.4 5.2 4.6 6.4 6 7 L7 6.2 L9.5 7.8 L8.4 9.5 C4.2 9.3 0.7 5.8 0.5 1.6 Z"/></svg>
        (555) 214-3800</span>
      <span class="contact">
        <svg viewBox="0 0 10 10" aria-hidden="true"><rect x="2.5" y="0.5" width="5" height="3"/><rect x="0.5" y="3.5" width="9" height="4" rx="1"/><rect x="2.5" y="6.5" width="5" height="3"/></svg>
        (555) 214-3815</span>
      <span class="contact">
        <svg viewBox="0 0 10 10" aria-hidden="true"><path d="M0.5 2 H9.5 V8.5 H0.5 Z M0.8 2.3 L5 5.6 L9.2 2.3" stroke="#f7f7f6" stroke-width=".8"/></svg>
        codyharlan@brenwicksrvs.com</span>
      <span class="contact">
        <svg viewBox="0 0 10 10" aria-hidden="true"><path d="M0.5 3 C2 1 8 1 9.5 3 L8.5 4.5 L7 3.8 V3 C6 2.6 4 2.6 3 3 V3.8 L1.5 4.5 Z M2 5 H8 L9 9 H1 Z"/></svg>
        (555) 407-6218</span>
      <span class="contact">
        <svg viewBox="0 0 10 10" aria-hidden="true"><path d="M5 0.3 C2.9 0.3 1.5 1.9 1.5 3.7 C1.5 6.2 5 9.7 5 9.7 C5 9.7 8.5 6.2 8.5 3.7 C8.5 1.9 7.1 0.3 5 0.3 Z M5 2.4 A1.3 1.3 0 1 1 5 5 A1.3 1.3 0 1 1 5 2.4 Z"/></svg>
        Carlow, OK 73855</span>
      <span class="contact">
        <svg viewBox="0 0 10 10" aria-hidden="true"><circle cx="5" cy="5" r="4.5"/><path d="M0.5 5 H9.5 M5 0.5 C3 3 3 7 5 9.5 M5 0.5 C7 3 7 7 5 9.5" stroke="#f7f7f6" stroke-width=".7" fill="none"/></svg>
        www.brenwicksrvs.com</span>
    </div>
  </section>

</main>
</body>
</html>
```